Business Cards for new orthopaedic surgery practice

My husband and I are starting our own orthopaedic surgery practice. We are looking for a business card that is uniform, but one will have my name/title and the other will have his. You can just create one design with my name on it for now. But when I choose your design as the winning design I will ask that you add another copy with his name/title.

We are looking for classy, simple, elite all in one. We like dark blues/a little gold/yellow. Something that goes with our logo. We want our logo incorporated. Here is all the info you need:
Business name: RV Bone & Vitality Center
Location: 38517 North Willowmere Ave
Coral Springs, FL 33071
Phone: 954-218-4063
Fax: 954-582-7341
Email: info@myrvbonecare.example

Names: Lydia Vance, M.D.
Board Certified Hand and Upper Extremity Surgeon

Ebo Dansu, M.D.
Board Certified Hip & Knee Replacement/General Orthopaedic Surgeon

Can decide what you want to put on the back. Maybe a slogan:
Rooted in Care. Focused on You

I am just going to upload our logo. The only thing is if we select you as the winning design, the location, and phone numbers may change. We will need your help to update that once fully solidified.

Industry/Entity Type

Medical

Contact Information for Business Card

Colors
0054AA
0677BA
7BADD7
CADEEF
E8F1F8
0094D4
00A9DD
6FCCEA
C7EBF8
E9F6FB

Requirements
Must have
• class, appeal,
Should not have
• We want to air on the side of masculine if we are looking at masculine vs. feminine feel. But we still want it classy, sophisticated, and something we will love

```html
<!DOCTYPE html>
<html lang="en">
<head>
<meta charset="utf-8">
<title>RV Bone &amp; Vitality Center — Business Card</title>
<link href="https://fonts.googleapis.com/css2?family=Montserrat:wght@400;500;700&display=swap" rel="stylesheet">
<style>
  :root {
    --backdrop: #2c2c2e;
    --navy: #1b2a52;
    --navy-deep: #16233f;
    --navy-emboss: #2a3b66;
    --gold: #c9a35c;
    --ink: #1d2b55;
    --text: #2a2f3a;
    --paper: #ffffff;
    --slogan: #dfe5f2;
  }
  * { box-sizing: border-box; margin: 0; padding: 0; }
  html, body { width: 1200px; height: 689px; overflow: hidden; }
  body {
    background: var(--backdrop);
    font-family: "Montserrat", sans-serif;
    position: relative;
  }
  .card {
    position: absolute;
    top: 190px;
    width: 540px;
    height: 309px;
    border-radius: 24px;
    overflow: hidden;
  }
  /* Back side */
  .card-back {
    left: 40px;
    background: linear-gradient(115deg, #3a4a72 0%, var(--navy) 38%, var(--navy-deep) 100%);
  }
  .back-name {
    position: absolute;
    left: 0; right: 0;
    top: 118px;
    text-align: center;
    white-space: nowrap;
    font-weight: 700;
    font-size: 24px;
    color: var(--navy-emboss);
    letter-spacing: 0.5px;
  }
  .slogan {
    position: absolute;
    left: 0; right: 0;
    bottom: 54px;
    text-align: center;
    font-size: 13px;
    font-weight: 400;
    color: var(--slogan);
    letter-spacing: 0.3px;
  }
  /* Front side */
  .card-front {
    left: 620px;
    background: var(--paper);
  }
  .front-name {
    position: absolute;
    right: 28px;
    top: 30px;
    white-space: nowrap;
    font-weight: 700;
    font-size: 15px;
    color: var(--ink);
  }
  .person {
    position: absolute;
    left: 30px;
    top: 112px;
  }
  .person-name {
    font-weight: 700;
    font-size: 27px;
    color: var(--ink);
    line-height: 1.1;
    margin-bottom: 8px;
    white-space: nowrap;
  }
  .person-title {
    font-size: 12.5px;
    color: var(--text);
    line-height: 1.45;
  }
  .contact {
    position: absolute;
    left: 30px;
    bottom: 26px;
    list-style: none;
  }
  .contact li {
    display: flex;
    align-items: center;
    gap: 9px;
    font-size: 12.5px;
    color: var(--text);
    line-height: 1.65;
    white-space: nowrap;
  }
  .contact svg { width: 12px; height: 12px; fill: var(--ink); flex: none; }
  .address {
    position: absolute;
    right: 28px;
    bottom: 26px;
    text-align: right;
    font-style: normal;
    font-size: 11.5px;
    color: var(--text);
    line-height: 1.55;
    white-space: nowrap;
  }
  .address .practice {
    font-weight: 500;
    color: var(--ink);
    font-size: 12.5px;
  }
</style>
</head>
<body>

  <section class="card card-back" aria-label="Card back">
    <p class="back-name">RV Bone &amp; Vitality Center</p>
    <p class="slogan">Rooted in Care. Focused on You</p>
  </section>

  <section class="card card-front" aria-label="Card front">
    <p class="front-name">RV Bone &amp; Vitality Center</p>

    <div class="person">
      <h1 class="person-name">Ebo Dansu, M.D.</h1>
      <p class="person-title">Board Certified Hip &amp; Knee Replacement<br>General Orthopaedic Surgeon</p>
    </div>

    <ul class="contact">
      <li>
        <svg viewBox="0 0 24 24" aria-hidden="true"><path d="M6.6 10.8a15.1 15.1 0 0 0 6.6 6.6l2.2-2.2a1 1 0 0 1 1-.25 11.4 11.4 0 0 0 3.6.57 1 1 0 0 1 1 1V20a1 1 0 0 1-1 1A17 17 0 0 1 3 4a1 1 0 0 1 1-1h3.5a1 1 0 0 1 1 1c0 1.25.2 2.45.57 3.57a1 1 0 0 1-.25 1z"/></svg>
        954-218-4063
      </li>
      <li>
        <svg viewBox="0 0 24 24" aria-hidden="true"><path d="M6 2h10v5H6zM3 8h18v9h-3v5H6v-5H3zm5 7v5h8v-5z"/></svg>
        954-582-7341
      </li>
      <li>
        <svg viewBox="0 0 24 24" aria-hidden="true"><path d="M2 5h20v14H2zm2 2v.5l8 5 8-5V7z"/></svg>
        info@myrvbonecare.example
      </li>
    </ul>

    <address class="address">
      <span class="practice">RV Bone &amp; Vitality Center</span><br>
      38517 North Willowmere Ave<br>
      Coral Springs, FL 33071
    </address>
  </section>

</body>
</html>
```